Need Business Card for our Real Estate Business with Sales Executive's Picture

PANTONE 484 C ( RED)

PANTONE 2766 C ( BLUE

Industry/Entity Type

Real Estate

Contact Information for Business Card

Name, Mobile, email, & picture of Person
Agency Phone, address, Web address

Requirements
Must have
• Our Logo Colours, Agent Picture,

```html
<!DOCTYPE html>
<html lang="en">
<head>
<meta charset="utf-8">
<title>Merida – Business Card</title>
<link href="https://fonts.googleapis.com/css2?family=Cinzel:wght@500&family=Tinos&family=Roboto:wght@400&display=swap" rel="stylesheet">
<style>
  :root {
    --navy: #0b1437;
    --paper: #f2f2f2;
    --backdrop: #e4e4e4;
    --accent-red: #7a1a1a;
    --white: #ffffff;
  }
  html, body {
    margin: 0; padding: 0;
    width: 1200px; height: 960px;
    overflow: hidden;
    background: var(--backdrop);
  }
  .canvas { position: relative; width: 1200px; height: 960px; }

  .card { position: absolute; width: 600px; height: 343px; box-shadow: 0 2px 4px rgba(0,0,0,.35); }

  /* Front */
  .card-front { left: 314px; top: 113px; background: var(--paper); overflow: hidden; }
  .front-band { position: absolute; left: 0; top: 173px; width: 600px; height: 151px; background: var(--navy); }
  .brand-front {
    position: absolute; left: 36px; top: 100px;
    display: flex; align-items: center; gap: 10px;
    font-family: "Cinzel", serif; font-weight: 500;
    font-size: 40px; letter-spacing: 2px; color: var(--navy);
  }
  .brand-mark { width: 12px; height: 12px; background: var(--accent-red); }
  .address {
    position: absolute; left: 36px; top: 188px;
    font-family: "Tinos", serif; font-size: 15px; line-height: 18px; color: var(--white);
  }
  .contact-list {
    position: absolute; left: 36px; top: 232px; margin: 0; padding: 0; list-style: none;
    font-family: "Tinos", serif; font-size: 15px; line-height: 19px; color: var(--white);
  }
  .contact-list li { display: flex; align-items: center; gap: 9px; }
  .contact-list svg { width: 13px; height: 13px; fill: var(--white); flex: none; }
  .agent-photo {
    position: absolute; left: 396px; top: 68px; width: 138px; height: 167px;
    border: 1px solid var(--navy); border-radius: 10px;
    background: linear-gradient(180deg, #d9d9d9 0%, #c9c9cc 45%, #1e3a8a 75%, #142a6b 100%);
  }
  .agent-name {
    position: absolute; left: 376px; top: 256px; width: 180px; text-align: center;
    font-family: "Cinzel", serif; color: var(--white);
  }
  .agent-name .name { font-size: 22px; line-height: 26px; }
  .agent-name .role { font-family: "Tinos", serif; font-size: 16px; letter-spacing: 1px; line-height: 20px; }

  /* Back */
  .card-back { left: 311px; top: 472px; background: var(--navy); }
  .brand-back {
    position: absolute; left: 0; right: 0; top: 186px;
    display: flex; justify-content: center; align-items: center; gap: 14px;
    font-family: "Cinzel", serif; font-weight: 500;
    font-size: 46px; letter-spacing: 3px; color: var(--white);
  }
  .brand-back .brand-mark { width: 14px; height: 14px; }
  .web-back {
    position: absolute; left: 0; right: 0; top: 297px; text-align: center;
    font-family: "Roboto", sans-serif; font-size: 14px; letter-spacing: 3.5px; color: var(--white);
  }
</style>
</head>
<body>
<div class="canvas">

  <section class="card card-front">
    <div class="front-band"></div>
    <div class="brand-front"><span class="brand-mark"></span>MERIDA</div>

    <div class="address">4120 Willow Crest Road<br>Fairview, Oregon 97024</div>

    <ul class="contact-list">
      <li><svg viewBox="0 0 24 24"><path d="M6.6 10.8a15.1 15.1 0 0 0 6.6 6.6l2.2-2.2c.3-.3.7-.4 1-.2 1.1.4 2.3.6 3.6.6.6 0 1 .4 1 1V20c0 .6-.4 1-1 1A17 17 0 0 1 3 4c0-.6.4-1 1-1h3.5c.6 0 1 .4 1 1 0 1.3.2 2.5.6 3.6.1.3 0 .7-.2 1z"/></svg>555 214 7730</li>
      <li><svg viewBox="0 0 24 24"><path d="M7 1h10a2 2 0 0 1 2 2v18a2 2 0 0 1-2 2H7a2 2 0 0 1-2-2V3a2 2 0 0 1 2-2zm0 3v14h10V4z"/></svg>555 390 6182</li>
      <li><svg viewBox="0 0 24 24"><path d="M2 5h20v14H2zm2 2v.5l8 5 8-5V7z"/></svg>daniel@merida.com</li>
      <li><svg viewBox="0 0 24 24"><circle cx="12" cy="12" r="10"/><path d="M8 6c2 1 1 3 3 4s0 4 2 5M15 4c-1 2 1 3 3 3" stroke="#0b1437" stroke-width="2" fill="none"/></svg>www.merida.com</li>
    </ul>

    <div class="agent-photo" role="img" aria-label="Portrait photo of the agent in a blue suit"></div>

    <div class="agent-name">
      <div class="name">DANIEL REYES</div>
      <div class="role">CEO/FOUNDER</div>
    </div>
  </section>

  <section class="card card-back">
    <div class="brand-back"><span class="brand-mark"></span>MERIDA</div>
    <div class="web-back">www.merida.com</div>
  </section>

</div>
</body>
</html>
```